The Kestrel Personal Training Studio Information Card

The front and back of card to give people that walk in to our gym. There are a few things to say on the card. But it also needs to be designed in an attractive way. You can make some of the information bullett points or with icons or graphics. Please look at our website at https://thekestreltraining.com/ . The card will be 4" x 9"

Target Market(s)

High End Clientele who want to train in a private gym

Industry/Entity Type

Fitness

Font styles to use
Serif
Sans Serif
Other font styles liked:
• the same font Borvale uses on the veltab

Colors
F0912C
F2A743
F7CA91
FBE8D2
FDF5EE

Requirements
Must have
• A cool look

```html
<!DOCTYPE html>
<html lang="en">
<head>
<meta charset="utf-8">
<title>The Kestrel Personal Training Studio – Information Card</title>
<link rel="stylesheet" href="https://fonts.googleapis.com/css2?family=Oswald:wght@500;600;700&family=Poppins:ital,wght@0,400;0,500;0,700;1,400&display=swap">
<style>
  :root {
    --orange: #f26539;
    --charcoal: #262626;
    --slate: #58595b;
    --white: #ffffff;
    --photo-warm: #b98a5c;
    --photo-cool: #c9ccd0;
  }
  * { box-sizing: border-box; margin: 0; padding: 0; }
  html, body { width: 1200px; height: 1200px; overflow: hidden; background: var(--white); }
  body { position: relative; font-family: "Poppins", sans-serif; }

  .card {
    position: absolute; top: 69px; width: 475px; height: 1069px;
    background: var(--orange); display: flex; flex-direction: column; overflow: hidden;
  }
  .card--front { left: 104px; }
  .card--back { left: 628px; }

  .top-band { height: 20px; background: var(--orange); flex: none; }

  .brand {
    background: var(--white); flex: none; height: 112px;
    display: flex; flex-direction: column; align-items: center; justify-content: center;
  }
  .brand__name {
    font-family: "Poppins", sans-serif; font-weight: 700; color: var(--slate);
    font-size: 44px; line-height: 1; letter-spacing: -1px; text-transform: uppercase;
  }
  .brand__name small { display: block; font-size: 17px; letter-spacing: 0; margin-bottom: 2px; }
  .brand__tagline {
    margin-top: 8px; font-family: "Poppins", sans-serif; font-weight: 700; color: var(--slate);
    font-size: 12px; letter-spacing: 5px; text-transform: uppercase;
  }

  .photo { flex: none; }
  .photo--trainers { height: 397px; background: linear-gradient(180deg, #eef0f2 0%, var(--photo-cool) 55%, #7d7f83 100%); }
  .photo--session { height: 234px; background: linear-gradient(90deg, var(--photo-warm) 0%, #c99766 55%, #8a7a6e 100%); }

  .band-dark { background: var(--charcoal); color: var(--white); flex: none; text-align: center; }
  .headline { font-family: "Oswald", sans-serif; font-weight: 600; text-transform: uppercase; letter-spacing: 1.5px; }

  .front-heading { height: 149px; display: flex; align-items: center; justify-content: center; }
  .front-heading .headline { font-size: 33px; line-height: 33px; }

  .copy {
    color: var(--white); text-align: center; font-size: 15.6px; line-height: 19.8px; letter-spacing: 0.6px;
  }
  .front-copy { padding: 28px 40px 0; }
  .front-copy p + p { margin-top: 15px; }

  .web-box {
    position: absolute; left: 65px; bottom: 0; width: 345px; height: 70px; background: var(--white);
    display: flex; align-items: center; justify-content: center;
    color: var(--orange); font-weight: 700; font-size: 19.5px; letter-spacing: 0.8px;
  }

  .back-heading { height: 69px; display: flex; align-items: center; justify-content: center; }
  .back-heading .headline { font-size: 36px; letter-spacing: 1px; }

  .back-copy { height: 177px; padding: 16px 28px 0; flex: none; }

  .rates { height: 308px; padding-top: 10px; }
  .rates__title { color: var(--orange); font-size: 36px; line-height: 48px; }
  .rates__note { font-style: italic; font-size: 19px; letter-spacing: 1px; margin-top: 6px; }
  .rates__list { list-style: none; margin: 20px auto 0; width: 390px; text-align: left; font-size: 19.5px; letter-spacing: 0.8px; }
  .rates__list li { display: flex; line-height: 33px; }
  .rates__freq { width: 192px; }
  .rates__price { color: var(--orange); font-weight: 700; }
  .rates__partner { color: var(--orange); font-weight: 700; font-size: 17.5px; letter-spacing: 0.6px; margin-top: 14px; }
  .rates__example { font-size: 12.5px; line-height: 16px; letter-spacing: 0.4px; margin-top: 12px; }

  .contact { color: var(--white); text-align: center; padding-top: 20px; font-size: 20px; line-height: 23px; letter-spacing: 0.8px; }
  .contact__web { font-weight: 700; margin-top: 10px; font-size: 19.5px; }
</style>
</head>
<body>

  <section class="card card--front">
    <div class="top-band"></div>
    <header class="brand">
      <div class="brand__name"><small>The</small>Kestrel</div>
      <div class="brand__tagline">Private Training Studio</div>
    </header>
    <div class="photo photo--trainers" role="img" aria-label="Photo of two trainers working out with rope equipment in the gym"></div>
    <div class="band-dark front-heading">
      <h1 class="headline">A safe and<br>individualized approach<br>to strength training</h1>
    </div>
    <div class="copy front-copy">
      <p>Our clients have different goals: Build strength, Increase Flexibility, Improve functional and daily movements, Train for an event, or Weight Loss. We will tailor your training program to the specific results you are looking for.</p>
      <p>Some ways of training increase the chance of injury, we do not practice those types of training at The Kestrel. Many of our clients have current or past injuries that can cause problems. We work with them to not aggravate those injuries or allow them to become an obstacle to their workouts.</p>
    </div>
    <div class="web-box">thekestreltraining.com</div>
  </section>

  <section class="card card--back">
    <div class="top-band"></div>
    <header class="brand">
      <div class="brand__name"><small>The</small>Kestrel</div>
      <div class="brand__tagline">Private Training Studio</div>
    </header>
    <div class="photo photo--session" role="img" aria-label="Photo of a trainer coaching a client using suspension straps against a wood-panelled wall"></div>
    <div class="band-dark back-heading">
      <h2 class="headline">How do you get started?</h2>
    </div>
    <div class="copy back-copy">
      We schedule prospective clients for a no cost or obligation consultation. At that consultation we will do a movement screen with you. This will allow the trainer to see what level of flexibility and strength you are currently at. You will be able to discuss your goals and other issues (injuries, etc) at that time.
    </div>
    <div class="band-dark rates">
      <h3 class="headline rates__title">Our Rates</h3>
      <p class="rates__note">All Sessions are 60 minutes</p>
      <ul class="rates__list">
        <li><span class="rates__freq">1 time per week</span><span>— <span class="rates__price">$110</span> per session</span></li>
        <li><span class="rates__freq">2 times per week</span><span>— <span class="rates__price">$85</span> per session</span></li>
        <li><span class="rates__freq">3 times per week</span><span>— <span class="rates__price">$80</span> per session</span></li>
      </ul>
      <p class="rates__partner">Add $40 for a Partnered Session</p>
      <p class="rates__example">Example: A Partnered Session (2 people training together)<br>coming twice a week is $125 per session</p>
    </div>
    <div class="contact">
      <p>482 Larch Avenue, Durham, NC</p>
      <p>contact@thekestreltraining.com</p>
      <p>919.555.0142</p>
      <p class="contact__web">thekestreltraining.com</p>
    </div>
  </section>

</body>
</html>
```